Signage Design Project

We need a logo and signage for the shopfront of a personal fitness training gym and coaching facility. We want the signage to cover the glass shopfront windows which consist of 4 glass windows with dimensions: 1 of 200cm x 180cm, 2 of 180cm x 135cm and 1 of 180cm x 180cm. The windows that are 200x 180 and 180x180 are the most visable/ important. We want the 200x180 to display the logo and our name which is "Ridgeline Fitness Centre" with further information of: Your personal training studio and boutique coaching gym Ph: 9471 2836.
For the window with 180 x 180cm measurement we want to list the services we provide which are:
Personal Training Sessions | Group Classes|Weight Loss |Toning & Sculpting|Bodybuilding I Cardio|Weights| Kettlebells| Boxing| Circuits I Team Building Programs| Boot Camp I Healthy Lifestyle & Wellness Coaching
The 2 windows 180x135cm are diagonal to the entry of the shop. We want them to be the same and plainer in design with the words: Ridgeline Fitness Centre
Personal Training Studio and Boutique Coaching Gym
The signage design also includes an acrylic window box that lights up which is to display the logo and Ridgeline Fitness Centre

```html
<!DOCTYPE html>
<html lang="en">
<head>
<meta charset="utf-8">
<title>Ridgeline Fitness Centre – Window Signage</title>
<link href="https://fonts.googleapis.com/css2?family=Exo+2:wght@600;800&display=swap" rel="stylesheet">
<style>
  :root {
    --page-bg: #ffffff;
    --frame-grey: #8a8a8a;
    --panel-edge: #222222;
    --brand-teal: #1a9cbf;
    --deep-teal: #00718c;
    --lime: #a5b321;
    --white: #ffffff;
    --photo-light: #eef1f3;
    --photo-jacket: #3f97aa;
    --photo-top: #d9506b;
    --photo-trousers: #e3e7ea;
  }
  * { margin: 0; padding: 0; box-sizing: border-box; }
  html, body {
    width: 1200px;
    height: 900px;
    overflow: hidden;
    background: var(--page-bg);
  }
  .canvas {
    position: relative;
    width: 1200px;
    height: 900px;
    border: 1px solid var(--frame-grey);
    background: var(--page-bg);
  }
  .window-panel {
    position: absolute;
    left: 237px;
    top: 87px;
    width: 709px;
    height: 719px;
    border: 1px solid var(--panel-edge);
    background: var(--white);
    overflow: hidden;
  }
  .athlete-photo {
    position: absolute;
    left: 0;
    top: 71px;
    width: 426px;
    height: 602px;
    background: linear-gradient(165deg,
      var(--photo-light) 0%,
      var(--photo-light) 12%,
      var(--photo-jacket) 28%,
      var(--photo-top) 40%,
      var(--photo-jacket) 50%,
      var(--photo-trousers) 64%,
      var(--photo-light) 100%);
  }
  .panel-curves {
    position: absolute;
    inset: 0;
    width: 100%;
    height: 100%;
  }
  .brand-lockup {
    position: absolute;
    left: 255px;
    top: 302px;
    display: flex;
    align-items: center;
    gap: 14px;
    color: var(--brand-teal);
    font-family: "Exo 2", sans-serif;
    font-weight: 800;
  }
  .brand-dot {
    width: 96px;
    height: 96px;
    border-radius: 50%;
    background: var(--brand-teal);
    flex: none;
  }
  .brand-name {
    display: flex;
    flex-direction: column;
    line-height: 1;
  }
  .brand-name .primary {
    font-size: 60px;
    letter-spacing: 1px;
    text-transform: uppercase;
  }
  .brand-name .secondary {
    font-size: 28px;
    letter-spacing: 2px;
    margin-top: 6px;
  }
  .brand-details {
    position: absolute;
    left: 365px;
    top: 418px;
    width: 320px;
    color: var(--deep-teal);
    font-family: "Exo 2", sans-serif;
  }
  .brand-details .tagline {
    font-weight: 600;
    font-size: 15px;
    line-height: 1.3;
  }
  .brand-details .phone {
    margin-top: 8px;
    font-weight: 800;
    font-size: 22px;
    letter-spacing: 1px;
    color: var(--brand-teal);
  }
  .corner-name {
    position: absolute;
    left: 24px;
    top: 650px;
    color: var(--white);
    font-family: "Exo 2", sans-serif;
    font-weight: 800;
    font-size: 14px;
    line-height: 1.1;
    width: 90px;
  }
</style>
</head>
<body>
  <main class="canvas">
    <section class="window-panel">
      <div class="athlete-photo" role="img" aria-label="Photo of a female dancer in a teal jacket, red top and white trousers leaping with her head thrown back"></div>

      <svg class="panel-curves" viewBox="0 0 709 719" preserveAspectRatio="none" aria-hidden="true">
        <path d="M0,490 C170,615 410,705 650,688 L620,719 L0,719 Z" fill="var(--lime)"/>
        <path d="M0,545 C190,665 420,720 640,700" fill="none" stroke="var(--white)" stroke-width="6"/>
        <path d="M709,438 C680,570 610,670 440,719 L709,719 Z" fill="var(--deep-teal)"/>
      </svg>

      <div class="brand-lockup">
        <span class="brand-dot"></span>
        <span class="brand-name">
          <span class="primary">Ridgeline</span>
          <span class="secondary">Fitness Centre</span>
        </span>
      </div>

      <div class="brand-details">
        <p class="tagline">Your personal training studio<br>and boutique coaching gym</p>
        <p class="phone">Ph: 9471 2836</p>
      </div>

      <div class="corner-name">Ridgeline Fitness</div>
    </section>
  </main>
</body>
</html>
```